SOLVE Study flyer

I need help designing a flyer for a research study that will include brain imaging in adolescents. The info is in the attached document. The study is called the Sequoia Outlook Lantern Valley Echo (SOLVE) study. Ideally this would be returned as a document that I can edit in the future as we will have several new recruitment phases (different age groups, etc. I also would love to have a logo designed as part of this project, but I recognize that might be a separate design request.

```html
<!DOCTYPE html>
<html lang="en">
<head>
<meta charset="utf-8">
<title>SOLVE Study Flyer</title>
<link rel="stylesheet" href="https://fonts.googleapis.com/css2?family=Oswald:wght@600;700&family=Poppins:wght@500;600;700;800&family=Alegreya+SC:ital,wght@1,700&family=Roboto+Condensed:wght@500;700&display=swap">
<style>
  :root {
    --stage: #383838;
    --forest: #063806;
    --title-green: #0b6a0b;
    --lime-top: #b4ff8e;
    --lime-soft: #d9ffc9;
    --mint: #f2fff0;
    --accent-lime: #b8ff8c;
    --ring: #6f9a63;
    --white: #ffffff;
  }
  * { margin: 0; padding: 0; box-sizing: border-box; }
  html, body { width: 984px; height: 1200px; overflow: hidden; background: var(--stage); }
  .flyer {
    position: absolute; left: 160px; top: 102px; width: 664px; height: 995px;
    overflow: hidden; font-family: "Poppins", sans-serif; color: var(--forest);
    background: linear-gradient(180deg, var(--lime-top) 0%, var(--lime-soft) 25%);
  }
  .band-top { position: absolute; left: 0; top: 249px; width: 664px; height: 200px; background: var(--forest); }
  .body-panel {
    position: absolute; left: 0; top: 449px; width: 664px; height: 454px;
    background: radial-gradient(ellipse at 30% 30%, var(--mint) 0%, var(--lime-soft) 60%, var(--accent-lime) 100%);
  }
  .band-bottom { position: absolute; left: 0; top: 903px; width: 664px; height: 92px; background: var(--forest); }
  .study-title {
    position: absolute; left: 0; top: 16px; width: 664px; text-align: center;
    font-family: "Oswald", sans-serif; font-weight: 700; font-size: 29px; line-height: 32px;
    letter-spacing: -0.5px; color: var(--title-green); text-transform: uppercase;
  }
  .hero-photo {
    position: absolute; left: 102px; top: 132px; width: 454px; height: 233px; border-radius: 26px;
    background: linear-gradient(160deg, #c9d3de 0%, #6f8fa6 45%, #c99a74 100%);
  }
  .headline-parent {
    position: absolute; left: 0; top: 372px; width: 664px; text-align: center;
    color: var(--white); font-weight: 800; font-size: 34px; letter-spacing: -0.3px;
  }
  .age-tag {
    position: absolute; left: 216px; top: 428px; width: 233px; height: 65px;
    background: var(--mint); border: 6px solid var(--forest); border-radius: 12px;
    text-align: center; font-weight: 800; font-size: 32px; line-height: 53px; color: var(--forest);
  }
  .headline-worry {
    position: absolute; left: 0; top: 505px; width: 664px; text-align: center;
    font-weight: 800; font-size: 33px; line-height: 41px; letter-spacing: -0.3px;
  }
  .intro {
    position: absolute; left: 30px; top: 594px; width: 620px; text-align: center;
    font-weight: 700; font-size: 15.5px; line-height: 24px;
  }
  .section-bar {
    position: absolute; left: 29px; top: 682px; width: 348px; height: 38px;
    background: var(--forest); border-radius: 4px; color: var(--white);
    font-weight: 700; font-size: 17.5px; line-height: 38px; padding-left: 19px;
  }
  .steps { position: absolute; left: 32px; top: 730px; width: 340px; list-style: none; }
  .steps li { position: relative; padding-left: 29px; font-weight: 500; font-size: 13.2px; line-height: 16px; margin-bottom: 17px; }
  .steps li svg { position: absolute; left: 0; top: 1px; }
  .eligibility-ring { position: absolute; left: 380px; top: 662px; }
  .eligibility {
    position: absolute; left: 395px; top: 676px; width: 256px; height: 256px; border-radius: 50%;
    background: var(--forest);
  }
  .eligibility h2 {
    position: absolute; left: 0; top: 20px; width: 256px; text-align: center;
    color: var(--accent-lime); font-weight: 700; font-size: 18.5px; line-height: 23.5px;
  }
  .criteria { position: absolute; left: 35px; top: 108px; width: 200px; list-style: none; }
  .criteria li { position: relative; padding-left: 22px; color: var(--white); font-weight: 500; font-size: 11.6px; line-height: 14px; margin-bottom: 16px; }
  .criteria li svg { position: absolute; left: 0; top: 0; }
  .contact-prompt {
    position: absolute; left: 29px; top: 910px; color: var(--white);
    font-family: "Alegreya SC", serif; font-style: italic; font-weight: 700; font-size: 16px; line-height: 22px;
  }
  .compensation {
    position: absolute; left: 271px; top: 884px; width: 114px; height: 114px; border-radius: 50%;
    background: var(--lime-soft); border: 2px dotted var(--forest); outline: 3px solid var(--lime-soft);
    text-align: center; font-family: "Roboto Condensed", sans-serif; color: var(--forest);
  }
  .compensation .label { display: block; margin-top: 20px; font-weight: 500; font-size: 14px; line-height: 17px; }
  .compensation .amount { display: block; font-weight: 700; font-size: 26px; line-height: 34px; }
  .email {
    position: absolute; left: 410px; top: 938px; width: 245px; height: 30px; border-radius: 15px;
    background: var(--mint); text-align: center; font-weight: 500; font-size: 14.5px; line-height: 30px;
  }
</style>
</head>
<body>
<main class="flyer">
  <div class="band-top"></div>
  <div class="body-panel"></div>
  <div class="band-bottom"></div>

  <h1 class="study-title">Sequoia Outlook Lantern<br>Valley Echo</h1>
  <div class="hero-photo" role="img" aria-label="Photo of three young people drawing together with coloured pencils at a table"></div>

  <p class="headline-parent">ARE YOU THE PARENT &nbsp;OF A CHILD</p>
  <div class="age-tag">AGE 10-17?</div>
  <p class="headline-worry">DO THEY WORRY OR OVERTHINK<br>NEGATIVE EMOTIONS?</p>
  <p class="intro">Northfield University researchers are seeking girls age 10-17 for a study about brain activity in emotions and decision-making and how they relate to puberty, anxiety and depression.</p>

  <div class="section-bar">STUDY PARTICIPATION INVOLVES</div>
  <ul class="steps">
    <li><svg width="20" height="16" viewBox="0 0 20 16"><path d="M8 1 L15 8 L8 15 L1 8 Z M13 1 L20 8 L13 15" fill="none" stroke="#063806" stroke-width="1.5"/><path d="M8 5 L11 8 L8 11 L5 8 Z" fill="#063806"/></svg>One one-hour interview (online or in-person) where your child will discuss their thoughts</li>
    <li><svg width="20" height="16" viewBox="0 0 20 16"><path d="M8 1 L15 8 L8 15 L1 8 Z M13 1 L20 8 L13 15" fill="none" stroke="#063806" stroke-width="1.5"/><path d="M8 5 L11 8 L8 11 L5 8 Z" fill="#063806"/></svg>Online questionnaires (parent and child)</li>
    <li><svg width="20" height="16" viewBox="0 0 20 16"><path d="M8 1 L15 8 L8 15 L1 8 Z M13 1 L20 8 L13 15" fill="none" stroke="#063806" stroke-width="1.5"/><path d="M8 5 L11 8 L8 11 L5 8 Z" fill="#063806"/></svg>One two-hour visit where your child will complete an MRI scan, answer questions about their puberty stage, and have a small hair sample taken to study puberty hormones</li>
  </ul>

  <svg class="eligibility-ring" width="290" height="290" viewBox="0 0 290 290"><path d="M145 10 A135 135 0 0 1 250 230" fill="none" stroke="var(--ring)" stroke-width="14"/></svg>
  <section class="eligibility">
    <h2>YOUR CHILD<br>MAY BE<br>ELIGIBLE IF THEY</h2>
    <ul class="criteria">
      <li><svg width="17" height="17" viewBox="0 0 17 17"><circle cx="8" cy="9" r="7" fill="none" stroke="#fff" stroke-width="1.5"/><path d="M4.5 8.5 L7.5 11.5 L15 3" fill="none" stroke="#fff" stroke-width="1.8"/></svg>Are age 10-17</li>
      <li><svg width="17" height="17" viewBox="0 0 17 17"><circle cx="8" cy="9" r="7" fill="none" stroke="#fff" stroke-width="1.5"/><path d="M4.5 8.5 L7.5 11.5 L15 3" fill="none" stroke="#fff" stroke-width="1.8"/></svg>Tend to worry or overthink negative thoughts</li>
      <li><svg width="17" height="17" viewBox="0 0 17 17"><circle cx="8" cy="9" r="7" fill="none" stroke="#fff" stroke-width="1.5"/><path d="M4.5 8.5 L7.5 11.5 L15 3" fill="none" stroke="#fff" stroke-width="1.8"/></svg>Have not been diagnosed with psychosis, learning problems,or autism</li>
    </ul>
  </section>

  <p class="contact-prompt">Interested in participating?<br>Want more information?<br>Please contact us!</p>
  <div class="compensation"><span class="label">Compensation<br>Up to</span><span class="amount">$140</span></div>
  <div class="email">solvestudy@northfieldhealth.edu</div>
</main>
</body>
</html>
```